Veltrane Group Business Card Design

The CEO is looking for a new trendy look for his business card.
You can stay with current branding or come up with something new/creative. It can be 3D, including Medical Office buildings. You can use our logo in a variety of colors. Please include name, title, company name, company website, email address, cell number

Target Market(s)

Real Estate Development and Construction

Industry/Entity Type

Health care real estate

Contact Information for Business Card

Rohesh Kamdar, CEO M-604.781.2249 E-roheshkamdar@veltrane.com Address:4180 Lindqvist Ave, Tampa, FL 33482 www.veltrane.com

Font styles to use
Other font styles liked:
• Be creative

Requirements
Must have
• Creative, trendy look
Nice to have
• Please go to our website to get a feel- www. veltrane.com
Should not have
• small fonts

```html
<!DOCTYPE html>
<html lang="en">
<head>
<meta charset="utf-8">
<title>Veltrane Group Business Card</title>
<link rel="stylesheet" href="https://fonts.googleapis.com/css2?family=Lato:wght@400;700;900&display=swap">
<style>
  :root {
    --stage: #2e2e2e;
    --card-white: #ffffff;
    --brand-red: #b21f2a;
    --brand-red-soft: #bd2c37;
    --text-light: #ffffff;
  }
  * { margin: 0; padding: 0; box-sizing: border-box; }
  html, body {
    width: 1200px; height: 689px; overflow: hidden;
    background: var(--stage);
    font-family: "Lato", sans-serif;
  }
  .stage {
    width: 1200px; height: 689px;
    display: flex; align-items: center; justify-content: center; gap: 40px;
  }
  .card {
    width: 540px; height: 308px;
    border-radius: 22px;
    position: relative; overflow: hidden;
    box-shadow: 0 18px 40px rgba(0,0,0,.45);
  }
  .card-front {
    background: var(--card-white);
    display: flex; align-items: center; justify-content: center;
  }
  .wordmark {
    font-weight: 900; font-size: 58px; letter-spacing: -1px;
    color: var(--brand-red); line-height: 1;
  }
  .card-back {
    background: var(--brand-red);
    color: var(--text-light);
  }
  .watermark {
    position: absolute; right: -30px; bottom: -42px;
    font-weight: 900; font-size: 150px; letter-spacing: -4px;
    color: var(--brand-red-soft); line-height: 1;
    white-space: nowrap;
  }
  .back-content {
    position: absolute; inset: 0;
    display: flex; align-items: center; justify-content: center;
    padding: 0 24px;
  }
  .identity { flex: 0 0 auto; text-align: right; }
  .name {
    font-weight: 900; font-size: 24px; letter-spacing: 1.2px;
    text-transform: uppercase; line-height: 1.1; white-space: nowrap;
  }
  .title { font-size: 15px; font-weight: 400; margin-top: 4px; letter-spacing: .5px; }
  .divider {
    width: 1px; height: 120px; background: var(--text-light);
    margin: 0 18px; flex: 0 0 auto;
  }
  .contacts { list-style: none; font-size: 13.5px; line-height: 1.25; flex: 0 0 auto; }
  .contacts li { display: flex; align-items: flex-start; gap: 8px; margin: 5px 0; white-space: nowrap; }
  .contacts svg { width: 13px; height: 13px; flex: 0 0 auto; margin-top: 1px; fill: var(--text-light); }
</style>
</head>
<body>
<main class="stage">
  <section class="card card-front">
    <span class="wordmark">Veltrane Group</span>
  </section>

  <section class="card card-back">
    <span class="watermark" aria-hidden="true">Veltrane</span>
    <div class="back-content">
      <div class="identity">
        <h1 class="name">Rohesh Kamdar</h1>
        <p class="title">President / CEO</p>
      </div>
      <div class="divider"></div>
      <ul class="contacts">
        <li>
          <svg viewBox="0 0 24 24"><path d="M12 1a8 8 0 0 0-8 8c0 6 8 14 8 14s8-8 8-14a8 8 0 0 0-8-8zm0 11a3 3 0 1 1 0-6 3 3 0 0 1 0 6z"/></svg>
          <span>4180 Lindqvist Ave<br>Tampa, FL 33482</span>
        </li>
        <li>
          <svg viewBox="0 0 24 24"><path d="M7 1h10a2 2 0 0 1 2 2v18a2 2 0 0 1-2 2H7a2 2 0 0 1-2-2V3a2 2 0 0 1 2-2zm0 3v14h10V4zm5 15.5a1.2 1.2 0 1 0 0 2.4 1.2 1.2 0 0 0 0-2.4z"/></svg>
          <span>604.781.2249</span>
        </li>
        <li>
          <svg viewBox="0 0 24 24"><path d="M2 5h20v14H2zm2 2v.5l8 5.5 8-5.5V7zm0 3v7h16v-7l-8 5.5z"/></svg>
          <span>roheshkamdar@veltrane.com</span>
        </li>
        <li>
          <svg viewBox="0 0 24 24"><path d="M12 1a11 11 0 1 0 0 22 11 11 0 0 0 0-22zm7.9 10h-3.9a17 17 0 0 0-1.3-6.7A9 9 0 0 1 19.9 11zM12 3.2c1 1.3 1.9 4 2 7.8h-4c.1-3.8 1-6.5 2-7.8zM9.3 4.3A17 17 0 0 0 8 11H4.1a9 9 0 0 1 5.2-6.7zM4.1 13H8a17 17 0 0 0 1.3 6.7A9 9 0 0 1 4.1 13zm7.9 7.8c-1-1.3-1.9-4-2-7.8h4c-.1 3.8-1 6.5-2 7.8zm2.7-1.1A17 17 0 0 0 16 13h3.9a9 9 0 0 1-5.2 6.7z"/></svg>
          <span>www.veltrane.com</span>
        </li>
      </ul>
    </div>
  </section>
</main>
</body>
</html>
```